Salon and Spa Distributor Business Card

Need a business card. We are are distributor in the salon and spa industry. We identify with natural beauty. Need a card with:
Company Name: Petal Quarry"
Title: "President & CEO"
Address
Company Phone number
email
website
Tag Line:" The Professional Salon Source"

Industry/Entity Type

Business

Contact Information for Business Card

Name: Dov Strommen
Title: "President & CEO"
Address: 31 Harlow Ln, Bexmoor, NJ 07813
Company Phone number: 800-463-5918
email: dovstrommen@petalquarry.example
website: www.petalquarry.example

Requirements
Should not have
• No black backgrounds

```html
<!DOCTYPE html>
<html lang="en">
<head>
<meta charset="utf-8">
<title>Petal Quarry – Business Card</title>
<link href="https://fonts.googleapis.com/css2?family=Questrial&display=swap" rel="stylesheet">
<style>
  :root {
    --backdrop: #4a403c;
    --card: #f5f2ea;
    --card-back: #e4ecd9;
    --card-edge: #ddd8cc;
    --green: #2f9e22;
    --green-deep: #23781a;
    --ink: #2e2e30;
    --ink-muted: #5c5c60;
  }
  * { box-sizing: border-box; margin: 0; padding: 0; }
  html, body {
    width: 1200px; height: 716px; overflow: hidden;
    background: var(--backdrop);
    font-family: "Questrial", "Century Gothic", sans-serif;
  }
  .stage { position: relative; width: 1200px; height: 716px; }
  .card {
    position: absolute; top: 215px;
    width: 500px; height: 286px;
    background: var(--card);
    border: 1px solid var(--card-edge);
    border-radius: 4px;
    box-shadow: 0 10px 24px rgba(0,0,0,.35);
  }

  /* Back side */
  .card--back {
    left: 70px; background: var(--card-back);
    display: flex; align-items: center; justify-content: center; gap: 12px;
  }
  .back-mark { width: 26px; height: 26px; border-radius: 50%; background: var(--green-deep); }
  .back-name { color: var(--green-deep); font-size: 30px; letter-spacing: .5px; }

  /* Front side */
  .card--front { left: 630px; }
  .brand { position: absolute; left: 30px; top: 32px; display: flex; align-items: center; gap: 12px; }
  .brand-dot { width: 46px; height: 46px; border-radius: 50%; background: var(--green); flex: none; }
  .brand-name { color: var(--green); font-size: 27px; line-height: 1; }
  .tagline { color: var(--ink); font-size: 12.5px; margin-top: 5px; }

  .person { position: absolute; left: 30px; top: 160px; }
  .person-name { color: var(--green); font-size: 20px; font-weight: 700; }
  .person-title { color: var(--ink-muted); font-size: 11.5px; margin-top: 4px; }

  .contact { position: absolute; left: 250px; top: 170px; list-style: none; }
  .contact li { display: flex; align-items: center; gap: 9px; color: var(--ink); font-size: 12.5px; height: 20px; white-space: nowrap; }
  .contact svg { width: 12px; height: 12px; flex: none; fill: var(--green); }
</style>
</head>
<body>
<main class="stage">

  <section class="card card--back" aria-label="Card back">
    <span class="back-mark"></span>
    <span class="back-name">Petal Quarry</span>
  </section>

  <section class="card card--front" aria-label="Card front">
    <div class="brand">
      <span class="brand-dot"></span>
      <div>
        <div class="brand-name">Petal Quarry</div>
        <div class="tagline">The Professional Salon Source</div>
      </div>
    </div>

    <div class="person">
      <div class="person-name">Dov Strommen</div>
      <div class="person-title">President &amp; CEO</div>
    </div>

    <ul class="contact">
      <li>
        <svg viewBox="0 0 24 24" aria-hidden="true"><path d="M6.6 10.8a15 15 0 0 0 6.6 6.6l2.2-2.2a1 1 0 0 1 1-.25 11.4 11.4 0 0 0 3.6.57 1 1 0 0 1 1 1V20a1 1 0 0 1-1 1A17 17 0 0 1 3 4a1 1 0 0 1 1-1h3.5a1 1 0 0 1 1 1c0 1.25.2 2.45.57 3.57a1 1 0 0 1-.25 1z"/></svg>
        800-463-5918
      </li>
      <li>
        <svg viewBox="0 0 24 24" aria-hidden="true"><path d="M2 5h20v14H2z M4 7v1l8 5 8-5V7l-8 5z" fill-rule="evenodd"/></svg>
        dovstrommen@petalquarry.example
      </li>
      <li>
        <svg viewBox="0 0 24 24" aria-hidden="true"><path d="M12 2a10 10 0 1 0 0 20 10 10 0 0 0 0-20zm0 2c1 1.3 1.8 3 2.1 5H9.9C10.2 7 11 5.3 12 4zM4.3 11h3.6a15 15 0 0 0 0 2H4.3a8 8 0 0 1 0-2zm5.6 2a13 13 0 0 1 0-2h4.2a13 13 0 0 1 0 2zm6.2 0a15 15 0 0 0 0-2h3.6a8 8 0 0 1 0 2zM12 20c-1-1.3-1.8-3-2.1-5h4.2c-.3 2-1.1 3.7-2.1 5z"/></svg>
        www.petalquarry.example
      </li>
      <li>31 Harlow Ln, Bexmoor, NJ 07813</li>
    </ul>
  </section>

</main>
</body>
</html>
```